Alterations to existing business card

Here is my current logo and I want the "cafe and bar" taken off with just the words Lumo and our slogan "Savour the moment" on the card, Plus the logo.
Our Current Business Card is currently 5.5cm by 5.5cm and would like it to remain like this thanks.
The loyalty card can be 10 squares with the logo specifying the 10th coffee free. I would like the cheapest option please.
Also on our business card would like the Facebook logo and instagram Logo with TAZALUMO27 as link to our photos on instagram.

Keep Colour schemes the same please.

On the business cards

Dale Brinton Director
0427916038
dale27lumo@mailvista.test

Paula Ferrisi Principal
0428571963
paulumo@mailvista.test

Thanks Dale

Industry/Entity Type

Business

```html
<!DOCTYPE html>
<html lang="en">
<head>
<meta charset="utf-8">
<title>Lumo — Business Card &amp; Loyalty Card</title>
<link rel="stylesheet" href="https://fonts.googleapis.com/css2?family=Questrial&family=Didact+Gothic&display=swap">
<style>
  :root {
    --backdrop: #4b4b4b;
    --card: #ffffff;
    --gold: #e9a53c;
    --ink: #111111;
    --grey-text: #555555;
    --pattern-cream: #fbf3e2;
    --stamp-fill: #1a1a1a;
  }
  * { box-sizing: border-box; margin: 0; padding: 0; }
  html, body {
    width: 1105px; height: 1200px; overflow: hidden;
    background: var(--backdrop);
  }
  body {
    position: relative;
    font-family: "Questrial", "Didact Gothic", sans-serif;
  }
  .card {
    position: absolute;
    width: 449px; height: 449px;
    background: var(--card);
  }
  /* Business card */
  .business-card { left: 124px; top: 110px; }
  .brand-badge {
    position: absolute; left: 62px; top: 41px;
    width: 144px; height: 144px; border-radius: 50%;
    border: 3px solid var(--gold);
    display: flex; align-items: center; justify-content: center;
    color: var(--gold); font-size: 34px; letter-spacing: 3px;
  }
  .brand-name {
    position: absolute; left: 38px; top: 196px;
    font-size: 60px; line-height: 1; letter-spacing: 2px;
    color: var(--ink);
  }
  .slogan {
    position: absolute; left: 40px; top: 252px;
    font-size: 13px; font-style: italic; letter-spacing: 1px;
    color: var(--gold); white-space: nowrap;
  }
  .person-name {
    position: absolute; left: 38px; top: 286px;
    font-size: 26px; letter-spacing: 0.5px; color: var(--gold);
  }
  .person-role {
    position: absolute; left: 38px; top: 322px;
    font-size: 19px; color: var(--ink);
  }
  .contact-list {
    position: absolute; left: 38px; top: 358px;
    list-style: none;
  }
  .contact-item {
    display: flex; align-items: center; gap: 10px;
    font-size: 19px; color: var(--grey-text);
    height: 28px; white-space: nowrap;
  }
  .contact-icon { width: 18px; height: 18px; flex: none; }

  /* Loyalty card */
  .loyalty-card { left: 500px; top: 630px; overflow: hidden; }
  .pattern-field {
    position: absolute; inset: 0;
    background: var(--pattern-cream);
  }
  .loyalty-badge {
    position: absolute; left: 135px; top: 33px;
    width: 166px; height: 166px; border-radius: 50%;
    border: 4px solid var(--ink); background: var(--card);
    display: flex; align-items: center; justify-content: center;
    font-size: 40px; letter-spacing: 4px; color: var(--ink);
  }
  .stamp-grid {
    position: absolute; left: 37px; top: 221px;
    display: grid; grid-template-columns: repeat(5, 66px);
    column-gap: 7px; row-gap: 17px;
  }
  .stamp {
    width: 66px; height: 66px; border-radius: 50%;
    border: 2px solid var(--ink); background: var(--card);
    display: flex; align-items: center; justify-content: center;
  }
  .stamp-mark {
    width: 46px; height: 46px; border-radius: 50%;
    background: var(--stamp-fill); opacity: 0.12;
  }
  .stamp--free {
    background: var(--gold);
    font-size: 19px; color: var(--ink); font-weight: 700;
  }
  .social-line {
    position: absolute; left: 40px; right: 40px; top: 398px;
    display: flex; align-items: center; gap: 8px;
  }
  .rule { flex: 1; height: 1px; background: var(--grey-text); }
  .social-dot {
    width: 17px; height: 17px; border-radius: 50%; background: var(--gold);
  }
  .social-handle {
    font-size: 18px; letter-spacing: 1px; color: var(--grey-text);
  }
</style>
</head>
<body>

<section class="card business-card">
  <div class="brand-badge">LUMO</div>
  <div class="brand-name">LUMO</div>
  <div class="slogan">SAVOUR THE MOMENT</div>
  <div class="person-name">DALE BRINTON</div>
  <div class="person-role">DIRECTOR</div>
  <ul class="contact-list">
    <li class="contact-item">
      <svg class="contact-icon" viewBox="0 0 18 18" aria-hidden="true">
        <rect x="4" y="1" width="10" height="16" rx="2" fill="none" stroke="#e9a53c" stroke-width="2"/>
        <line x1="7" y1="14" x2="11" y2="14" stroke="#e9a53c" stroke-width="1.5"/>
      </svg>
      0427916038
    </li>
    <li class="contact-item">
      <svg class="contact-icon" viewBox="0 0 18 18" aria-hidden="true">
        <rect x="1" y="4" width="16" height="11" fill="#e9a53c"/>
        <polyline points="1,4 9,10 17,4" fill="none" stroke="#ffffff" stroke-width="1.5"/>
      </svg>
      dale27lumo@mailvista.test
    </li>
  </ul>
</section>

<section class="card loyalty-card">
  <div class="pattern-field" role="img" aria-label="Faint repeating brand pattern in pale cream"></div>
  <div class="loyalty-badge">LUMO</div>
  <div class="stamp-grid">
    <div class="stamp"><div class="stamp-mark" role="img" aria-label="Coffee cup stamp icon"></div></div>
    <div class="stamp"><div class="stamp-mark" role="img" aria-label="Coffee cup stamp icon"></div></div>
    <div class="stamp"><div class="stamp-mark" role="img" aria-label="Coffee cup stamp icon"></div></div>
    <div class="stamp"><div class="stamp-mark" role="img" aria-label="Coffee cup stamp icon"></div></div>
    <div class="stamp"><div class="stamp-mark" role="img" aria-label="Coffee cup stamp icon"></div></div>
    <div class="stamp"><div class="stamp-mark" role="img" aria-label="Coffee cup stamp icon"></div></div>
    <div class="stamp"><div class="stamp-mark" role="img" aria-label="Coffee cup stamp icon"></div></div>
    <div class="stamp"><div class="stamp-mark" role="img" aria-label="Coffee cup stamp icon"></div></div>
    <div class="stamp"><div class="stamp-mark" role="img" aria-label="Coffee cup stamp icon"></div></div>
    <div class="stamp stamp--free">FREE</div>
  </div>
  <div class="social-line">
    <span class="rule"></span>
    <span class="social-dot"></span>
    <span class="social-handle">TAZALUMO27</span>
    <span class="rule"></span>
  </div>
</section>

</body>
</html>
```